Stationery Design Project

Hi All,

We need you to design stationary for a new Business and Accounting Advisory Firm. We have already got the logo designed and it is attached. If you could also if possible, match the fonts in your design to that on the logo’s provided.

What we need:
- Business Card
- A4 Letter head
- A4 Folders
- PPT template (Title page and regular page)

And what ever else you want to throw in.

We are in the process of getting the web site designed, however below is a list of websites which we like which will give you an understanding of the style that we are going for.

- plivant.example
- moldrabay.example
- tarvenhook.example
- quillorbank.example

I look forward to your seeing your design.
Updates

Hi All,

I have just realised that I forgot that i need to include a Sworn Ledgerkeepers image on the letter head, please find attaced as File 1. Could you please have this image in the bottom left header.

Regards,

Marcus

Industry/Entity Type

Business

Requirements
Must have
• Outputs:
- Documents ready to print
- Generic editable information
- Pdf copies of the documents
- Word version of letterhead

```html
<!DOCTYPE html>
<html lang="en">
<head>
<meta charset="utf-8">
<title>Halvorn Group – Letterhead</title>
<link rel="stylesheet" href="https://fonts.googleapis.com/css2?family=Source+Sans+3:wght@400;600&display=swap">
<style>
  :root {
    --brand-blue: #34589a;
    --brand-cyan: #3ebfe0;
    --brand-orange: #f7931e;
    --brand-amber: #fbb03b;
    --paper: #ffffff;
    --sans: "Source Sans 3", Arial, sans-serif;
  }
  html, body {
    margin: 0;
    padding: 0;
    overflow: hidden;
    background: var(--paper);
  }
  .letterhead {
    position: relative;
    width: 927px;
    height: 1200px;
    background: var(--paper);
    overflow: hidden;
  }
  .brand {
    position: absolute;
    left: 62px;
    top: 52px;
    height: 90px;
    display: flex;
    align-items: center;
    gap: 22px;
  }
  .brand-dot {
    width: 90px;
    height: 90px;
    border-radius: 50%;
    background: var(--brand-cyan);
    flex: none;
  }
  .brand-name {
    margin: 0;
    font-family: var(--sans);
    font-weight: 600;
    font-size: 42px;
    line-height: 1;
    color: var(--brand-blue);
    white-space: nowrap;
  }
  .contact {
    position: absolute;
    left: 718px;
    top: 62px;
    margin: 0;
    font-family: var(--sans);
    font-style: normal;
    font-size: 14px;
    line-height: 18px;
    color: var(--brand-blue);
  }
  .contact p { margin: 0 0 18px; }
  .footer-rule {
    position: absolute;
    top: 1154px;
    height: 6px;
  }
  .footer-rule--blue {
    left: 0;
    width: 542px;
    background: linear-gradient(90deg, var(--brand-cyan), var(--brand-blue));
  }
  .footer-rule--orange {
    left: 785px;
    width: 142px;
    background: linear-gradient(90deg, var(--brand-orange), var(--brand-amber));
  }
  .footer-web {
    position: absolute;
    left: 560px;
    top: 1147px;
    font-family: var(--sans);
    font-size: 16px;
    line-height: 20px;
    color: var(--brand-blue);
    white-space: nowrap;
  }
</style>
</head>
<body>
  <main class="letterhead">
    <header class="brand">
      <div class="brand-dot" aria-hidden="true"></div>
      <h1 class="brand-name">Halvorn Group</h1>
    </header>

    <address class="contact">
      <p>1234 Street Address<br>City, State 12345</p>
      <p>P: (123) 456-7890<br>F: (123) 987-6543</p>
    </address>

    <footer>
      <div class="footer-rule footer-rule--blue"></div>
      <span class="footer-web">www.halvorngroup.example</span>
      <div class="footer-rule footer-rule--orange"></div>
    </footer>
  </main>
</body>
</html>
```